Luxury Wine Label for New Startup Winery

We need a wine label for our new winery startup. We have worked with a local designer but do not feel the resulting label / logo have the elevation required to present our brand as a luxury wine. Our winery is called "Quailbrook Vineyards" and we are focused on extremely high quality hand crafted artisan and estate wines from the Pacific Northwest.
We would like to see designs that utilize a tree line, or other imagery that represents the "Quailbrook" part of our company name. Another interesting feature could be wood grain.
A logo will be required based on your design so please design with this in mind:
This logo should be consistent with the wine bottle label design, and should be representative of our high end exclusive wine while giving a sense of place (Oregon/ Pacific Northwest.)
I will supply an image of the design we received from our local designer, PLEASE NOTE: in general we do like wood grain and tree line concepts but feel the execution was poorly done.
ATTN: Logo design should be suitable for use on: Bottles (Red wine/rose/white wine), Bussiness cards, vehicle signage, business signage, etc
P.S.:
If you have a design that is not outside the box we are still interested in seeing it.
Label is for a burgundy style bottle with a label height of 3.5 - 4" and a width of 3.5-4"
any label <= 4"x4" and >=3.5"x3.5" will be acceptable:
HOWEVER Width should be greater than or equal to height due to the bottle format
Target Market(s)
Wine enthusiasts with adequate discretionary budgets to afford $100 bottles of wine.
Industry/Entity Type
Wine / Winery
Requirements
Must have
- A sense of luxury, a feel of exclusivity, and a theme consistent with our product and brand name
Nice to have
- Tree line, wood grain or other wood themes. Serif fonts
Should not have
- anything cheesy, off topic, hard to read script fonts or anything that makes the label hard to read from a few feet away or too busy

```html
<!DOCTYPE html>
<html lang="en">
<head>
<meta charset="utf-8">
<title>Quailbrook Vineyards – Wine Label</title>
<link rel="stylesheet" href="https://fonts.googleapis.com/css2?family=Cinzel:wght@400;500&family=Cormorant+Garamond:wght@500&display=swap">
<style>
  :root {
    --backdrop: #c8ae98;
    --label-paper: #f3f3f1;
    --label-ink: #1b1b1b;
    --title-silver: #d9d9d6;
    --accent-gold: #b8914a;
    --tree-dark: #222222;
    --tree-mid: #7a7a78;
  }
  * { margin: 0; padding: 0; box-sizing: border-box; }
  html, body {
    width: 1200px;
    height: 1200px;
    overflow: hidden;
    background: var(--backdrop);
  }
  .wine-label {
    position: absolute;
    left: 100px;
    top: 100px;
    width: 1000px;
    height: 1000px;
    background: var(--label-ink);
    overflow: hidden;
  }
  .label-sky {
    position: absolute;
    left: 0; top: 0;
    width: 100%;
    height: 380px;
    background: var(--label-paper);
  }
  .treeline-art {
    position: absolute;
    left: 60px;
    top: 70px;
    width: 880px;
    height: 330px;
    background: linear-gradient(180deg,
      rgba(243,243,241,0) 0%,
      rgba(122,122,120,0.35) 35%,
      var(--tree-mid) 65%,
      var(--tree-dark) 88%,
      var(--label-ink) 100%);
  }
  .brand-name {
    position: absolute;
    left: 0;
    width: 100%;
    text-align: center;
    font-family: "Cinzel", serif;
    color: var(--title-silver);
    line-height: 1;
  }
  .brand-name--primary {
    top: 570px;
    font-size: 92px;
    font-weight: 500;
    letter-spacing: 2px;
  }
  .brand-name--secondary {
    top: 680px;
    font-size: 52px;
    font-weight: 400;
    letter-spacing: 4px;
  }
  .origin-row {
    position: absolute;
    top: 770px;
    left: 0;
    width: 100%;
    height: 64px;
    display: flex;
    justify-content: center;
    align-items: center;
    gap: 36px;
    font-family: "Cormorant Garamond", serif;
    font-size: 24px;
    letter-spacing: 2px;
    color: var(--accent-gold);
  }
  .origin-mark {
    width: 64px;
    height: 64px;
    border: 2px solid var(--accent-gold);
    border-radius: 50%;
  }
  .varietal {
    position: absolute;
    top: 858px;
    left: 0;
    width: 100%;
    text-align: center;
    font-family: "Cormorant Garamond", serif;
    font-size: 26px;
    line-height: 34px;
    letter-spacing: 2px;
    color: var(--title-silver);
  }
  .fine-print {
    position: absolute;
    top: 942px;
    left: 0;
    width: 100%;
    text-align: center;
    font-family: "Cormorant Garamond", serif;
    font-size: 22px;
    letter-spacing: 2px;
    color: var(--accent-gold);
  }
</style>
</head>
<body>
  <main class="wine-label">
    <div class="label-sky"></div>
    <div class="treeline-art" role="img" aria-label="Silhouette of a Pacific Northwest fir tree line rising above a grassy ridge"></div>

    <h1 class="brand-name brand-name--primary">QUAILBROOK</h1>
    <p class="brand-name brand-name--secondary">VINEYARDS</p>

    <div class="origin-row">
      <span class="origin-region">OREGON</span>
      <span class="origin-mark"></span>
      <span class="origin-estate">ESTATE</span>
    </div>

    <p class="varietal">PINOT NOIR<br>WILLAMETTE VALLEY</p>

    <p class="fine-print">HANDCRAFTED ESTATE WINE · 750 ML</p>
  </main>
</body>
</html>
```